Biz Card

MARKETING today is the most rapidly changing business discipline. Media options to reach customers, actual customer preferences and consumer buying decisions change by the minute . . . no, by the second. The behavioral data generated by all aspects of the business and the new technologies that put the data to work together produce the potential to generate business intelligence and guide smart resource allocation to influence purchase and retention. However, to realize this potential, marketing professionals at all levels and in all organizations must continuously improve their skills not just from on-the-job training but by learning from masters in the field. The Bright Horizon Guild is the training center that serves this professional development need.model logos:msi.orgama.orgcontentmarketinginstitute.comBook covers on MarketingMetrics, Marketing Anaytics
Industry/Entity Type
Business
Contact Information for Business Card
Roy A. YoungCEOMarketing Science Academyphone: 310-601-4755email: roy@marketingscience.comAddress:437 South Rexford DriveBeverly Hills, CA 89377
Look and feel
Each slider illustrates characteristics of the customer's brand and the style your logo design should communicate.

```html
<!DOCTYPE html>
<html lang="en">
<head>
<meta charset="utf-8">
<title>Bright Horizon Guild – Business Card</title>
<link rel="stylesheet" href="https://fonts.googleapis.com/css2?family=Roboto:wght@400;500;700&display=swap">
<style>
  :root {
    --backdrop: #3a3230;
    --card-white: #f7f7f7;
    --card-black: #121212;
    --brand-red: #9b1c1f;
    --ink: #3d3d3d;
    --swoosh-dark: #4a4a4a;
    --swoosh-light: #b9b9b9;
    --emboss: #2a2a2a;
  }
  * { margin: 0; padding: 0; box-sizing: border-box; }
  html, body { width: 1200px; height: 716px; overflow: hidden; }
  body {
    background: var(--backdrop);
    font-family: "Roboto", sans-serif;
    display: flex;
    align-items: center;
    justify-content: center;
    gap: 40px;
  }
  .card {
    position: relative;
    width: 540px;
    height: 308px;
    overflow: hidden;
  }
  .card-back {
    background: var(--card-black);
    display: flex;
    align-items: center;
    justify-content: center;
  }
  .back-name {
    font-weight: 700;
    font-size: 30px;
    color: var(--emboss);
    letter-spacing: 0.5px;
  }
  .card-front { background: var(--card-white); }
  .wave { position: absolute; left: 0; top: 0; width: 540px; height: 308px; }
  .brand {
    position: absolute;
    left: 34px;
    top: 28px;
    display: flex;
    align-items: center;
    gap: 12px;
  }
  .brand-mark {
    width: 22px;
    height: 22px;
    background: var(--brand-red);
  }
  .brand-name {
    font-weight: 700;
    font-size: 27px;
    color: var(--brand-red);
  }
  .contact {
    position: absolute;
    left: 34px;
    top: 84px;
    list-style: none;
    font-size: 13px;
    color: var(--ink);
    line-height: 18px;
  }
  .contact li { display: flex; align-items: center; gap: 8px; }
  .contact .address { margin-bottom: 4px; }
  .contact svg { width: 11px; height: 11px; fill: var(--brand-red); flex: none; }
  .holder {
    position: absolute;
    right: 34px;
    bottom: 20px;
    text-align: right;
    color: #fff;
  }
  .holder-name { font-weight: 700; font-size: 20px; }
  .holder-title { font-size: 11px; margin-top: 6px; }
</style>
</head>
<body>
  <section class="card card-back">
    <p class="back-name">Bright Horizon Guild</p>
  </section>

  <section class="card card-front">
    <svg class="wave" viewBox="0 0 540 308" aria-hidden="true">
      <path d="M0,200 C110,210 190,252 300,250 C400,248 470,220 540,208 L540,308 L0,308 Z" fill="var(--brand-red)"/>
      <path d="M0,176 C110,186 190,228 300,226 C400,224 470,196 540,184" fill="none" stroke="var(--swoosh-dark)" stroke-width="7"/>
      <path d="M0,187 C110,197 190,240 300,238 C400,236 470,208 540,196" fill="none" stroke="var(--swoosh-light)" stroke-width="4"/>
    </svg>

    <div class="brand">
      <span class="brand-mark"></span>
      <span class="brand-name">Bright Horizon Guild</span>
    </div>

    <ul class="contact">
      <li class="address">912 North Calloway Lane Beverly Hills, CA 89377</li>
      <li>
        <svg viewBox="0 0 24 24"><path d="M6.6 10.8a15 15 0 0 0 6.6 6.6l2.2-2.2a1 1 0 0 1 1-.25 11.4 11.4 0 0 0 3.6.57 1 1 0 0 1 1 1V20a1 1 0 0 1-1 1A17 17 0 0 1 3 4a1 1 0 0 1 1-1h3.5a1 1 0 0 1 1 1c0 1.25.2 2.45.57 3.6a1 1 0 0 1-.25 1z"/></svg>
        310-555-0182
      </li>
      <li>
        <svg viewBox="0 0 24 24"><path d="M2 5h20v14H2z M2 5l10 8 10-8" fill="none" stroke="var(--brand-red)" stroke-width="2.5"/></svg>
        neil@brighthorizonguild.com
      </li>
      <li>
        <svg viewBox="0 0 24 24"><circle cx="12" cy="12" r="10"/></svg>
        www.brighthorizonguild.com
      </li>
    </ul>

    <div class="holder">
      <p class="holder-name">Neil P. Barton</p>
      <p class="holder-title">CEO</p>
    </div>
  </section>
</body>
</html>
```